Small legal and financial translation company needs Squarespace website, brochure and logo

Hello,
We are Lumarin Services (www.lumarinservices-example.com), a boutique legal and financial translation company. We offer our services mainly to Spanish customers. Our primary line of business is the translation of financial statements, but we translate a wide variety legal and financial texts.
The project we are offering comprises three parts: a redo of the current website, an informational brochure for potential customer and a logo design. These three parts should provide a consistent image. We would develop content soon.
We are looking for a website that would look like a typical law firm website, nothing too fancy. Right now, it is in English, Spanish and French, although the new site need only be in English and Spanish. There must be good toggling between the English and Spanish versions. There would be no need for tie-ins to social media and it would not contain a blog. Basically, a static site. We aren't interesting in driving traffic to the site or SEO, as we will contact nearly all potential customers beforehand. The website must be built in Squarespace to enable a smooth transition. The content would be similar to the current page, we'll be working on the exact content, but a rough draft is attached.
The brochure will be some three pages and would introduce the company to potential customers, using similar images as the website and the logo to be designed.
The only specifications for the logo is, as the website and brochure, it convey a sense of security and trust.
Feel free to ask with any questions as this is the first time we have used this platform.
Thank you!
Updates

I've added a more or less final version for the text in the brochure and updated the brief. Added Wednesday, June 10, 2015

Target Market(s)

Spanish law firms, auditors, accountants, banks, investment firms

Industry/Entity Type

Finance

Logo Text

Lumarin Services

Number of Pages Required

5+ page

Font styles to use
Serif

Requirements
Must have
• The website must be built in Squarespace and have a good option to toggle between English and Spanish versions.
• Brochure must be in both English and Spanish, I'm attaching a rough draft of the information that it will probably have. This should give an idea about what to include and the spacing. I will update it to include the final information.
Nice to have
• Would be nice to have some quality finance- and legal-related images
Should not have
• Vibrant colours

```html
<!DOCTYPE html>
<html lang="en">
<head>
<meta charset="utf-8">
<title>Lumarin Services – Brochure Spread</title>
<link rel="stylesheet" href="https://fonts.googleapis.com/css2?family=Playfair+Display:ital,wght@1,700&family=Sorts+Mill+Goudy&display=swap">
<style>
  :root {
    --backdrop: #e4e1dc;
    --page-dark: #1c1c1c;
    --page-mid: #3a3a3a;
    --photo-light: #dcdad8;
    --photo-dark: #3b3734;
    --brand-green: #1f8a4c;
    --brand-green-deep: #0f5a2f;
    --text-light: #ececec;
    --text-body: #d4d4d4;
    --rule: #f2f2f2;
  }
  * { margin: 0; padding: 0; box-sizing: border-box; }
  html, body { width: 1200px; height: 537px; overflow: hidden; }
  body { background: var(--backdrop); position: relative; font-family: "Sorts Mill Goudy", Georgia, serif; }

  .spread {
    position: absolute; left: 48px; top: 72px; width: 1112px; height: 394px;
    box-shadow: 0 2px 8px rgba(0,0,0,.25);
  }
  .page-cover {
    position: absolute; left: 0; top: 0; width: 556px; height: 394px;
    background: linear-gradient(160deg, var(--photo-light) 0%, #a9a49f 40%, var(--photo-dark) 75%, #2a2725 100%);
  }
  .page-benefits {
    position: absolute; left: 556px; top: 0; width: 556px; height: 394px;
    background: radial-gradient(ellipse at 45% 20%, var(--page-mid) 0%, var(--page-dark) 70%);
    overflow: hidden;
  }
  .green-band {
    position: absolute; left: 0; bottom: 0; width: 1112px; height: 12px;
    background: linear-gradient(90deg, var(--brand-green-deep), var(--brand-green) 40%, var(--brand-green-deep));
  }

  .brand-name {
    position: absolute; left: 52px; top: 20px;
    font-size: 11px; color: var(--brand-green); letter-spacing: .5px;
  }

  .section-title {
    position: absolute; right: 24px;
    font-family: "Playfair Display", Georgia, serif; font-style: italic; font-weight: 700;
    line-height: 1; color: var(--text-light); white-space: nowrap;
  }
  .section-title.en { top: 28px; font-size: 20px; }
  .section-title.es { top: 203px; font-size: 16.5px; }
  .section-rule { position: absolute; right: 24px; height: 2px; background: var(--rule); }
  .section-rule.en { top: 52px; width: 482px; }
  .section-rule.es { top: 223px; width: 275px; }

  .benefit-list { position: absolute; left: 264px; top: 0; list-style: none; }
  .benefit {
    position: absolute; left: 0; height: 28px; margin-top: -14px;
    display: flex; align-items: center; gap: 6px; white-space: nowrap;
  }
  .benefit-icon { width: 21px; height: 21px; flex: none; }
  .benefit-text { font-size: 10.2px; line-height: 11.5px; color: var(--text-body); }

  .photo { position: absolute; left: 51px; width: 116px; height: 72px; }
  .photo.handshake { top: 218px; background: linear-gradient(135deg, #151515, #5a5a5a 55%, #1e1e1e); }
  .photo.caller { top: 302px; background: linear-gradient(135deg, #cfcfcf, #6e6e6e 50%, #2c2c2c); }
</style>
</head>
<body>
<svg width="0" height="0" style="position:absolute">
  <defs>
    <symbol id="icon-tick" viewBox="0 0 22 22"><circle cx="11" cy="11" r="11" fill="#1f8a4c"/><circle cx="12.5" cy="11" r="4.5" fill="none" stroke="#fff" stroke-width="1.4"/><path d="M10.5 11l1.5 1.5 2.8-3" fill="none" stroke="#fff" stroke-width="1.4"/></symbol>
    <symbol id="icon-chat" viewBox="0 0 22 22"><circle cx="11" cy="11" r="11" fill="#1f8a4c"/><rect x="5" y="6" width="8" height="6" rx="2" fill="none" stroke="#fff" stroke-width="1.3"/><rect x="9" y="10" width="8" height="6" rx="2" fill="#1f8a4c" stroke="#fff" stroke-width="1.3"/></symbol>
    <symbol id="icon-badge" viewBox="0 0 22 22"><circle cx="11" cy="11" r="11" fill="#1f8a4c"/><circle cx="11" cy="10" r="4.5" fill="none" stroke="#fff" stroke-width="1.4"/><path d="M8.5 14l-1 4 3.5-2 3.5 2-1-4" fill="none" stroke="#fff" stroke-width="1.2"/></symbol>
    <symbol id="icon-voice" viewBox="0 0 22 22"><circle cx="11" cy="11" r="11" fill="#1f8a4c"/><circle cx="9" cy="9" r="2.5" fill="#fff"/><path d="M5 16c0-3 2-4.5 4-4.5s4 1.5 4 4.5z" fill="#fff"/><rect x="12" y="5" width="6" height="4" rx="1" fill="#fff"/></symbol>
    <symbol id="icon-screen" viewBox="0 0 22 22"><circle cx="11" cy="11" r="11" fill="#1f8a4c"/><rect x="5.5" y="6" width="11" height="8" fill="none" stroke="#fff" stroke-width="1.4"/><path d="M11 14v3M8 17h6" stroke="#fff" stroke-width="1.4"/></symbol>
  </defs>
</svg>

<div class="spread">
  <div class="page-cover" role="img" aria-label="Black and white photograph looking up at glass office skyscrapers"></div>

  <div class="page-benefits">
    <div class="brand-name">Lumarin Services</div>

    <h2 class="section-title en">Benefits of working with us:</h2>
    <div class="section-rule en"></div>
    <ul class="benefit-list en">
      <li class="benefit" style="top:72px"><svg class="benefit-icon"><use href="#icon-tick"/></svg><span class="benefit-text">Translations entrusted to a specialist company<br>save both time and money</span></li>
      <li class="benefit" style="top:98px"><svg class="benefit-icon"><use href="#icon-chat"/></svg><span class="benefit-text">Guaranteed quality time and time again</span></li>
      <li class="benefit" style="top:126px"><svg class="benefit-icon"><use href="#icon-badge"/></svg><span class="benefit-text">Promise that expert translators work only in<br>their mother tongue</span></li>
      <li class="benefit" style="top:155px"><svg class="benefit-icon"><use href="#icon-voice"/></svg><span class="benefit-text">A consistent voice cultivated over time and across<br>channels ensures that your firm speaks with one voice</span></li>
      <li class="benefit" style="top:181px"><svg class="benefit-icon"><use href="#icon-screen"/></svg><span class="benefit-text">Use of cutting-edge technology helps cut costs by<br>ensuring competitive budgets based on past work</span></li>
    </ul>

    <h2 class="section-title es" lang="es">Ventajas de trabajar con nosotros:</h2>
    <div class="section-rule es"></div>
    <ul class="benefit-list es" lang="es">
      <li class="benefit" style="top:243px"><svg class="benefit-icon"><use href="#icon-tick"/></svg><span class="benefit-text">Traducciones confiados a una empresa especializada<br>ahorran tiempo y dinero</span></li>
      <li class="benefit" style="top:269px"><svg class="benefit-icon"><use href="#icon-chat"/></svg><span class="benefit-text">Garantizado tiempo y tiempo de calidad de nuevo</span></li>
      <li class="benefit" style="top:298px"><svg class="benefit-icon"><use href="#icon-badge"/></svg><span class="benefit-text">Promesa de que expertos traductores trabajan<br>únicamente en su lengua materna</span></li>
      <li class="benefit" style="top:327px"><svg class="benefit-icon"><use href="#icon-voice"/></svg><span class="benefit-text">Una Voz coherente cultivada en el tiempo y en todos<br>los canales asegura que su empresa habla con una sola voz</span></li>
      <li class="benefit" style="top:359px"><svg class="benefit-icon"><use href="#icon-screen"/></svg><span class="benefit-text">Uso De la tecnología de vanguardia ayuda a reducir<br>costos, garantizando presupuestos competitivos<br>basado en trabajos anteriores</span></li>
    </ul>

    <div class="photo handshake" role="img" aria-label="Photograph of a business handshake across a desk"></div>
    <div class="photo caller" role="img" aria-label="Photograph of a businessman on the telephone at his desk"></div>
  </div>

  <div class="green-band"></div>
</div>
</body>
</html>
```